New Manager Resource Guide & Planner

I need a template designed for a resource guide and planner that new managers would use to help guide them their first year managing others. Think your typical planner injected with tips, worksheets, quotes and other helpful tools. Initially, I'd like a template created for some key pages: one month, one week and single day layouts plus a quote page. I'm attaching a very rudimentary idea of the project, just need it purposefully designed with my colors and branding. The size is 6" x 8 " h. I would like this done in InDesign or Keynote so I can edit it and create other pages. Most likely, though, will contract you to finish out the entire project.

Target Market(s)

new managers (and HR directors who will most likely purchase the resource planner for their employees)

Industry/Entity Type

Advertising

Font styles to use
Other font styles liked:
• archer, open sans

Requirements
Must have
• a creative feel to it (I come from the advertising industry, so a fun design is OK). use of my branding and colors, be noticeably well designed.
Nice to have
• look at other planners for ideas. my goal is to use your template to build out the other pages I need. So think cool edging, or stylized quote boxes, etc.
Should not have
• please use the colors in my palette in the attached pdf plus any other complementary colors you see fit. my branding uses the font archer, open sans, use these and any other fonts that you see fit.

```html
<!DOCTYPE html>
<html lang="en">
<head>
<meta charset="utf-8">
<title>New Manager Planner – Key Page Templates</title>
<link rel="stylesheet" href="https://fonts.googleapis.com/css2?family=Open+Sans:ital,wght@0,400;0,600;0,700;1,400&display=swap">
<style>
  :root{
    --purple:#5b3595;
    --lime:#e3e65a;
    --lime-deep:#c3cf2f;
    --olive:#8a8a32;
    --lavender:#e6dff0;
    --cream:#f4f6d6;
    --ink:#1d1d1d;
    --rule:#555555;
    --grid:#dcdcc8;
    --tab:#c9c9c9;
    --paper:#ffffff;
  }
  html,body{margin:0;padding:0;width:1200px;height:1200px;overflow:hidden;background:var(--paper);}
  .board{display:block;width:1200px;height:1200px;font-family:"Open Sans",sans-serif;}
  .page{fill:var(--paper);filter:url(#page-shadow);}
  .txt{font-family:"Open Sans",sans-serif;fill:var(--ink);}
  .label{font-size:13px;}
  .label-bold{font-size:11px;font-weight:700;}
  .time{font-size:12px;}
  .quote-small{font-size:13px;font-style:italic;}
  .date-num{font-size:19px;font-weight:600;fill:#fff;}
  .bar-label{font-size:12px;font-weight:700;fill:#fff;letter-spacing:.3px;}
  .day-num{font-size:13px;fill:#fff;}
  .day-name{font-size:13.5px;}
  .month-title{font-size:22px;font-weight:700;}
  .weekday{font-size:13px;font-weight:700;fill:#fff;}
  .tab-num{font-size:8px;fill:#555;}
  .notes-head{font-size:13px;font-weight:700;fill:var(--purple);}
  .tiny{font-size:8px;}
  .micro{font-size:3.5px;}
  .quote-big{font-size:23px;font-weight:700;}
  .dotted{stroke:var(--rule);stroke-width:.8;stroke-dasharray:1.5 1.5;fill:none;}
  .solid-gray{stroke:#8a8a8a;stroke-width:1;}
  .purple-rule{stroke:var(--purple);}
  .check{fill:none;stroke:var(--purple);stroke-width:1.3;}
  .ring{fill:none;stroke:var(--purple);stroke-width:1.2;}
  .grid-line{stroke:var(--grid);stroke-width:1.2;}
  .tab{fill:var(--tab);}
</style>
</head>
<body>
<svg class="board" viewBox="0 0 1500 1500" xmlns="http://www.w3.org/2000/svg">
  <defs>
    <filter id="page-shadow" x="-5%" y="-5%" width="110%" height="110%">
      <feDropShadow dx="0" dy="1" stdDeviation="4" flood-color="#8a88a8" flood-opacity=".35"/>
    </filter>
    <clipPath id="clip-day"><rect x="46" y="141" width="459" height="611"/></clipPath>
    <clipPath id="clip-week"><rect x="533" y="141" width="457" height="609"/></clipPath>
    <clipPath id="clip-sales"><rect x="1019" y="141" width="456" height="607"/></clipPath>
    <clipPath id="clip-month"><rect x="46" y="841" width="457" height="610"/></clipPath>
    <clipPath id="clip-plan"><rect x="533" y="841" width="457" height="610"/></clipPath>
    <pattern id="rules-17" patternUnits="userSpaceOnUse" width="3" height="17.3" y="961.5">
      <line x1="0" y1=".5" x2="3" y2=".5" class="dotted"/>
    </pattern>
    <pattern id="rules-18" patternUnits="userSpaceOnUse" width="3" height="18" y="961.5">
      <line x1="0" y1=".5" x2="3" y2=".5" class="dotted"/>
    </pattern>
    <pattern id="rules-notes" patternUnits="userSpaceOnUse" width="3" height="17" y="586.5">
      <line x1="0" y1=".5" x2="3" y2=".5" class="dotted"/>
    </pattern>
    <pattern id="rules-sales" patternUnits="userSpaceOnUse" width="3" height="19.4" y="299.5">
      <line x1="0" y1=".5" x2="3" y2=".5" class="dotted"/>
    </pattern>
    <pattern id="mini-grid" patternUnits="userSpaceOnUse" width="11" height="7" x="0" y="880">
      <rect x="2" y="2" width="6" height="2" fill="#bdbdbd"/>
    </pattern>
  </defs>

  <!-- ========== DAY PAGE (to-do) ========== -->
  <g class="day-page">
    <rect class="page" x="46" y="141" width="459" height="611"/>
    <g class="edge-accents" clip-path="url(#clip-day)">
      <circle cx="46" cy="752" r="175" fill="var(--lavender)"/>
      <rect x="491" y="300" width="14" height="120" rx="4" fill="var(--cream)"/>
      <rect x="491" y="430" width="14" height="120" rx="4" fill="var(--lavender)"/>
    </g>
    <rect x="54" y="149" width="229" height="100" fill="var(--lime)"/>
    <rect x="143" y="174" width="48" height="33" fill="var(--purple)"/>
    <text class="txt date-num" x="167" y="198" text-anchor="middle">19</text>
    <text class="txt label" x="72" y="242">Tuesday</text>
    <text class="txt label" x="224" y="242">March</text>
    <text class="txt quote-small" text-anchor="middle"><tspan x="394" y="176">Treat Employees like they</tspan><tspan x="394" y="196">make a difference and they</tspan><tspan x="394" y="216">will.</tspan></text>
    <line class="purple-rule" x1="54" y1="250" x2="497" y2="250" stroke-width="3"/>
    <text class="txt label-bold" x="59" y="268">Toda'y Schedule:</text>
    <text class="txt label-bold" x="287" y="268">To Do:</text>
    <g class="times">
      <text class="txt time" x="59" y="303">8:00</text><text class="txt time" x="59" y="327">9:00</text>
      <text class="txt time" x="59" y="355">10:00</text><text class="txt time" x="59" y="383">11:00</text>
      <text class="txt time" x="59" y="411">12:00</text><text class="txt time" x="59" y="439">1:00</text>
      <text class="txt time" x="59" y="467">2:00</text><text class="txt time" x="59" y="495">3:00</text>
      <text class="txt time" x="59" y="523">4:00</text><text class="txt time" x="59" y="551">5:00</text>
      <text class="txt time" x="59" y="579">6:00</text><text class="txt time" x="59" y="607">6:00</text>
      <text class="txt time" x="59" y="635">7:00</text><text class="txt time" x="59" y="657">8:00</text>
    </g>
    <g class="rows">
      <line class="dotted" x1="54" y1="310" x2="487" y2="310"/><line class="dotted" x1="54" y1="337" x2="487" y2="337"/>
      <line class="dotted" x1="54" y1="365" x2="487" y2="365"/><line class="dotted" x1="54" y1="392" x2="487" y2="392"/>
      <line class="dotted" x1="54" y1="420" x2="487" y2="420"/><line class="dotted" x1="54" y1="447" x2="487" y2="447"/>
      <line class="dotted" x1="54" y1="475" x2="487" y2="475"/><line class="dotted" x1="54" y1="503" x2="487" y2="503"/>
      <line class="dotted" x1="54" y1="530" x2="487" y2="530"/><line class="dotted" x1="54" y1="558" x2="487" y2="558"/>
      <line class="dotted" x1="54" y1="585" x2="487" y2="585"/><line class="dotted" x1="54" y1="613" x2="487" y2="613"/>
      <line class="dotted" x1="54" y1="641" x2="487" y2="641"/><line class="dotted" x1="54" y1="665" x2="497" y2="665"/>
    </g>
    <g class="checks">
      <rect class="check" x="286" y="290" width="12" height="12"/><rect class="check" x="286" y="318" width="12" height="12"/>
      <rect class="check" x="286" y="345" width="12" height="12"/><rect class="check" x="286" y="373" width="12" height="12"/>
      <rect class="check" x="286" y="400" width="12" height="12"/><rect class="check" x="286" y="428" width="12" height="12"/>
      <rect class="check" x="286" y="455" width="12" height="12"/><rect class="check" x="286" y="483" width="12" height="12"/>
      <rect class="check" x="286" y="511" width="12" height="12"/><rect class="check" x="286" y="538" width="12" height="12"/>
      <rect class="check" x="286" y="566" width="12" height="12"/><rect class="check" x="286" y="593" width="12" height="12"/>
      <rect class="check" x="286" y="621" width="12" height="12"/><rect class="check" x="286" y="649" width="12" height="12"/>
    </g>
    <rect x="54" y="669" width="223" height="18" fill="var(--purple)"/>
    <text class="txt bar-label" x="59" y="683">TONIGHT</text>
    <rect x="285" y="669" width="212" height="18" fill="var(--purple)"/>
    <text class="txt bar-label" x="289" y="683">GRATITUDE</text>
  </g>

  <!-- ========== WEEK PAGE ========== -->
  <g class="week-page">
    <rect class="page" x="533" y="141" width="457" height="609"/>
    <g class="edge-accents" clip-path="url(#clip-week)">
      <circle cx="990" cy="420" r="120" fill="var(--lavender)"/>
      <circle cx="533" cy="141" r="70" fill="var(--cream)"/>
    </g>
    <text class="txt label-bold" x="965" y="177" text-anchor="end" style="font-size:12px">March 2019</text>
    <line class="purple-rule" x1="541" y1="185" x2="982" y2="185" stroke-width="4"/>
    <g class="day">
      <circle cx="567" cy="209" r="16" fill="var(--olive)"/><text class="txt day-num" x="567" y="214" text-anchor="middle">18</text>
      <text class="txt day-name" x="590" y="213">Monday</text>
      <line class="dotted" x1="551" y1="232" x2="982" y2="232"/><line class="dotted" x1="551" y1="248" x2="982" y2="248"/><line class="dotted" x1="551" y1="264" x2="982" y2="264"/>
      <line class="solid-gray" x1="551" y1="279" x2="982" y2="279"/>
    </g>
    <g class="day">
      <circle cx="567" cy="297" r="16" fill="var(--olive)"/><text class="txt day-num" x="567" y="302" text-anchor="middle">19</text>
      <text class="txt day-name" x="590" y="302">Tuesday</text>
      <line class="dotted" x1="551" y1="320" x2="982" y2="320"/><line class="dotted" x1="551" y1="336" x2="982" y2="336"/><line class="dotted" x1="551" y1="352" x2="982" y2="352"/>
      <line class="solid-gray" x1="551" y1="369" x2="982" y2="369"/>
    </g>
    <g class="day">
      <circle cx="567" cy="387" r="16" fill="var(--olive)"/><text class="txt day-num" x="567" y="392" text-anchor="middle">20</text>
      <text class="txt day-name" x="590" y="391">Wednesday</text>
      <line class="dotted" x1="551" y1="408" x2="982" y2="408"/><line class="dotted" x1="551" y1="424" x2="982" y2="424"/><line class="dotted" x1="551" y1="440" x2="982" y2="440"/>
      <line class="solid-gray" x1="551" y1="456" x2="982" y2="456"/>
    </g>
    <g class="day">
      <circle cx="567" cy="475" r="16" fill="var(--olive)"/><text class="txt day-num" x="567" y="480" text-anchor="middle">21</text>
      <text class="txt day-name" x="590" y="478">Thusday</text>
      <line class="dotted" x1="551" y1="496" x2="982" y2="496"/><line class="dotted" x1="551" y1="512" x2="982" y2="512"/><line class="dotted" x1="551" y1="528" x2="982" y2="528"/>
      <line class="solid-gray" x1="551" y1="544" x2="982" y2="544"/>
    </g>
    <g class="day">
      <circle cx="567" cy="563" r="16" fill="var(--olive)"/><text class="txt day-num" x="567" y="568" text-anchor="middle">21</text>
      <text class="txt day-name" x="590" y="567">Friday</text>
      <line class="dotted" x1="551" y1="584" x2="982" y2="584"/><line class="dotted" x1="551" y1="600" x2="982" y2="600"/><line class="dotted" x1="551" y1="616" x2="982" y2="616"/>
      <line class="solid-gray" x1="551" y1="632" x2="982" y2="632"/>
    </g>
    <g class="day">
      <circle cx="567" cy="651" r="16" fill="var(--olive)"/><text class="txt day-num" x="567" y="656" text-anchor="middle">22</text>
      <text class="txt day-name" x="590" y="656">Saturday</text>
      <line class="dotted" x1="551" y1="683" x2="982" y2="683"/><line class="dotted" x1="551" y1="699" x2="982" y2="699"/><line class="dotted" x1="551" y1="715" x2="982" y2="715"/>
    </g>
    <line class="purple-rule" x1="541" y1="734" x2="982" y2="734" stroke-width="4"/>
  </g>

  <!-- ========== DAY PAGE (sales) ========== -->
  <g class="sales-day-page">
    <rect class="page" x="1019" y="141" width="456" height="607"/>
    <g class="edge-accents" clip-path="url(#clip-sales)">
      <circle cx="1475" cy="748" r="150" fill="var(--lavender)"/>
      <circle cx="1019" cy="470" r="60" fill="var(--cream)"/>
    </g>
    <rect x="1027" y="149" width="221" height="99" fill="var(--lime)"/>
    <rect x="1117" y="173" width="47" height="34" fill="var(--purple)"/>
    <text class="txt date-num" x="1140" y="197" text-anchor="middle">19</text>
    <text class="txt label" x="1045" y="241">Tuesday</text>
    <text class="txt label" x="1196" y="241">March</text>
    <text class="txt label" x="1260" y="164">Daily Goal</text>
    <line class="purple-rule" x1="1027" y1="249" x2="1468" y2="249" stroke-width="3"/>
    <line x1="1248" y1="249" x2="1248" y2="748" stroke="var(--ink)" stroke-width="1.3"/>
    <text class="txt label-bold" x="1033" y="268">Toda'y Schedule:</text>
    <text class="txt label-bold" x="1259" y="268">Sales Activity:</text>
    <g class="times">
      <text class="txt time" x="1033" y="302">8:00</text><text class="txt time" x="1033" y="326">9:00</text>
      <text class="txt time" x="1033" y="354">10:00</text><text class="txt time" x="1033" y="382">11:00</text>
      <text class="txt time" x="1033" y="410">12:00</text><text class="txt time" x="1033" y="438">1:00</text>
      <text class="txt time" x="1033" y="465">2:00</text><text class="txt time" x="1033" y="493">3:00</text>
      <text class="txt time" x="1033" y="521">4:00</text><text class="txt time" x="1033" y="549">5:00</text>
      <text class="txt time" x="1033" y="577">6:00</text><text class="txt time" x="1033" y="604">6:00</text>
      <text class="txt time" x="1033" y="632">7:00</text><text class="txt time" x="1033" y="654">8:00</text>
    </g>
    <g class="rows">
      <line class="dotted" x1="1027" y1="309" x2="1244" y2="309"/><line class="dotted" x1="1027" y1="336" x2="1244" y2="336"/>
      <line class="dotted" x1="1027" y1="364" x2="1244" y2="364"/><line class="dotted" x1="1027" y1="391" x2="1244" y2="391"/>
      <line class="dotted" x1="1027" y1="419" x2="1244" y2="419"/><line class="dotted" x1="1027" y1="446" x2="1244" y2="446"/>
      <line class="dotted" x1="1027" y1="474" x2="1244" y2="474"/><line class="dotted" x1="1027" y1="502" x2="1244" y2="502"/>
      <line class="dotted" x1="1027" y1="529" x2="1244" y2="529"/><line class="dotted" x1="1027" y1="557" x2="1244" y2="557"/>
      <line class="dotted" x1="1027" y1="584" x2="1244" y2="584"/><line class="dotted" x1="1027" y1="612" x2="1244" y2="612"/>
      <line class="dotted" x1="1027" y1="640" x2="1244" y2="640"/><line class="dotted" x1="1027" y1="662" x2="1244" y2="662"/>
    </g>
    <rect x="1027" y="665" width="217" height="18" fill="var(--purple)"/>
    <text class="txt bar-label" x="1032" y="679">TONIGHT</text>
    <rect x="1252" y="299" width="216" height="255" fill="url(#rules-sales)"/>
    <g class="sales-rings">
      <circle class="ring" cx="1260" cy="290" r="5"/><circle class="ring" cx="1260" cy="309" r="5"/>
      <circle class="ring" cx="1260" cy="329" r="5"/><circle class="ring" cx="1260" cy="348" r="5"/>
      <circle class="ring" cx="1260" cy="368" r="5"/><circle class="ring" cx="1260" cy="387" r="5"/>
      <circle class="ring" cx="1260" cy="406" r="5"/><circle class="ring" cx="1260" cy="426" r="5"/>
      <circle class="ring" cx="1260" cy="445" r="5"/><circle class="ring" cx="1260" cy="465" r="5"/>
      <circle class="ring" cx="1260" cy="484" r="5"/><circle class="ring" cx="1260" cy="503" r="5"/>
      <circle class="ring" cx="1260" cy="523" r="5"/><circle class="ring" cx="1260" cy="542" r="5"/>
    </g>
    <line x1="1252" y1="560" x2="1468" y2="560" stroke="var(--ink)" stroke-width="1.2"/>
    <text class="txt label" x="1254" y="574" style="font-size:12px">Notes</text>
    <rect x="1252" y="586" width="216" height="156" fill="url(#rules-notes)"/>
    <line class="dotted" x1="1271" y1="585" x2="1271" y2="742"/>
  </g>

  <!-- ========== MONTH PAGE ========== -->
  <g class="month-page">
    <rect class="page" x="46" y="841" width="457" height="610"/>
    <g class="edge-accents" clip-path="url(#clip-month)">
      <circle cx="503" cy="1160" r="110" fill="var(--cream)"/>
      <circle cx="46" cy="1451" r="95" fill="var(--cream)"/>
    </g>
    <rect x="54" y="849" width="441" height="38" fill="var(--lime-deep)"/>
    <text class="txt month-title" x="60" y="876">MONTH AT A GLANCE</text>
    <text class="txt label" x="487" y="873" text-anchor="end">March</text>
    <rect x="57" y="889" width="435" height="26" fill="var(--purple)"/>
    <g stroke="#fff" stroke-width="1.5">
      <line x1="119" y1="889" x2="119" y2="915"/><line x1="181" y1="889" x2="181" y2="915"/>
      <line x1="243" y1="889" x2="243" y2="915"/><line x1="305" y1="889" x2="305" y2="915"/>
      <line x1="367" y1="889" x2="367" y2="915"/><line x1="429" y1="889" x2="429" y2="915"/>
    </g>
    <text class="txt weekday" x="88" y="907" text-anchor="middle">Mon</text>
    <text class="txt weekday" x="150" y="907" text-anchor="middle">Tue</text>
    <text class="txt weekday" x="210" y="907" text-anchor="middle">Wed</text>
    <text class="txt weekday" x="274" y="907" text-anchor="middle">Thu</text>
    <text class="txt weekday" x="337" y="907" text-anchor="middle">Fri</text>
    <text class="txt weekday" x="399" y="907" text-anchor="middle">Sat</text>
    <text class="txt weekday" x="461" y="907" text-anchor="middle">Sun</text>
    <g class="grid">
      <line class="grid-line" x1="57" y1="915" x2="57" y2="1343"/><line class="grid-line" x1="119" y1="915" x2="119" y2="1343"/>
      <line class="grid-line" x1="181" y1="915" x2="181" y2="1343"/><line class="grid-line" x1="243" y1="915" x2="243" y2="1343"/>
      <line class="grid-line" x1="305" y1="915" x2="305" y2="1343"/><line class="grid-line" x1="367" y1="915" x2="367" y2="1343"/>
      <line class="grid-line" x1="429" y1="915" x2="429" y2="1343"/><line class="grid-line" x1="492" y1="915" x2="492" y2="1343"/>
      <line class="grid-line" x1="57" y1="987" x2="492" y2="987"/><line class="grid-line" x1="57" y1="1059" x2="492" y2="1059"/>
      <line class="grid-line" x1="57" y1="1130" x2="492" y2="1130"/><line class="grid-line" x1="57" y1="1201" x2="492" y2="1201"/>
      <line class="grid-line" x1="57" y1="1273" x2="492" y2="1273"/>
    </g>
    <g class="date-tabs">
      <rect class="tab" x="370" y="919" width="19" height="10"/><text class="tab-num" x="374" y="927">01</text>
      <rect class="tab" x="432" y="919" width="19" height="10"/><text class="tab-num" x="436" y="927">02</text>

      <rect class="tab" x="60" y="990" width="19" height="10"/><text class="tab-num" x="64" y="998">03</text>
      <rect class="tab" x="122" y="990" width="19" height="10"/><text class="tab-num" x="126" y="998">04</text>
      <rect class="tab" x="184" y="990" width="19" height="10"/><text class="tab-num" x="188" y="998">05</text>
      <rect class="tab" x="246" y="990" width="19" height="10"/><text class="tab-num" x="250" y="998">06</text>
      <rect class="tab" x="308" y="990" width="19" height="10"/><text class="tab-num" x="312" y="998">07</text>
      <rect class="tab" x="370" y="990" width="19" height="10"/><text class="tab-num" x="374" y="998">08</text>
      <rect class="tab" x="432" y="990" width="19" height="10"/><text class="tab-num" x="436" y="998">09</text>

      <rect class="tab" x="60" y="1062" width="19" height="10"/><text class="tab-num" x="64" y="1070">10</text>
      <rect class="tab" x="122" y="1062" width="19" height="10"/><text class="tab-num" x="126" y="1070">11</text>
      <rect class="tab" x="184" y="1062" width="19" height="10"/><text class="tab-num" x="188" y="1070">12</text>
      <rect class="tab" x="246" y="1062" width="19" height="10"/><text class="tab-num" x="250" y="1070">13</text>
      <rect class="tab" x="308" y="1062" width="19" height="10"/><text class="tab-num" x="312" y="1070">14</text>
      <rect class="tab" x="370" y="1062" width="19" height="10"/><text class="tab-num" x="374" y="1070">15</text>
      <rect class="tab" x="432" y="1062" width="19" height="10"/><text class="tab-num" x="436" y="1070">16</text>

      <rect class="tab" x="60" y="1133" width="19" height="10"/><text class="tab-num" x="64" y="1141">17</text>
      <rect class="tab" x="122" y="1133" width="19" height="10"/><text class="tab-num" x="126" y="1141">18</text>
      <rect class="tab" x="184" y="1133" width="19" height="10"/><text class="tab-num" x="188" y="1141">19</text>
      <rect class="tab" x="246" y="1133" width="19" height="10"/><text class="tab-num" x="250" y="1141">20</text>
      <rect class="tab" x="308" y="1133" width="19" height="10"/><text class="tab-num" x="312" y="1141">21</text>
      <rect class="tab" x="370" y="1133" width="19" height="10"/><text class="tab-num" x="374" y="1141">22</text>
      <rect class="tab" x="432" y="1133" width="19" height="10"/><text class="tab-num" x="436" y="1141">23</text>

      <rect class="tab" x="60" y="1204" width="19" height="10"/><text class="tab-num" x="64" y="1212">24</text>
      <rect class="tab" x="122" y="1204" width="19" height="10"/><text class="tab-num" x="126" y="1212">25</text>
      <rect class="tab" x="184" y="1204" width="19" height="10"/><text class="tab-num" x="188" y="1212">26</text>
      <rect class="tab" x="246" y="1204" width="19" height="10"/><text class="tab-num" x="250" y="1212">27</text>
      <rect class="tab" x="308" y="1204" width="19" height="10"/><text class="tab-num" x="312" y="1212">28</text>
      <rect class="tab" x="370" y="1204" width="19" height="10"/><text class="tab-num" x="374" y="1212">29</text>
      <rect class="tab" x="432" y="1204" width="19" height="10"/><text class="tab-num" x="436" y="1212">30</text>

      <rect class="tab" x="60" y="1276" width="19" height="10"/><text class="tab-num" x="64" y="1284">31</text>
    </g>
    <line class="purple-rule" x1="57" y1="1345" x2="492" y2="1345" stroke-width="3"/>
    <text class="txt notes-head" x="62" y="1368">Notes</text>
    <g stroke="var(--ink)" stroke-width="1">
      <line x1="120" y1="1370" x2="487" y2="1370"/>
      <line x1="62" y1="1396" x2="487" y2="1396"/>
      <line x1="62" y1="1422" x2="487" y2="1422"/>
    </g>
  </g>

  <!-- ========== MONTH PLANNING PAGE ========== -->
  <g class="month-plan-page">
    <rect class="page" x="533" y="841" width="457" height="610"/>
    <g class="edge-accents" clip-path="url(#clip-plan)">
      <circle cx="533" cy="1451" r="160" fill="var(--lavender)"/>
      <circle cx="990" cy="1150" r="55" fill="var(--cream)"/>
    </g>
    <text class="txt label-bold" x="543" y="861" style="font-size:11.5px">March 2019</text>
    <line class="purple-rule" x1="541" y1="869" x2="983" y2="869" stroke-width="3"/>
    <rect x="541" y="872" width="225" height="65" fill="var(--lime)"/>
    <text class="txt tiny" x="543" y="880">Big Picture</text>
    <line class="dotted" x1="547" y1="890" x2="750" y2="890"/>
    <line class="dotted" x1="547" y1="906" x2="750" y2="906"/>
    <line class="dotted" x1="547" y1="922" x2="750" y2="922"/>
    <g class="mini-calendars">
      <text class="txt micro" x="823" y="877" text-anchor="middle">November 2018</text>
      <rect x="780" y="880" width="86" height="48" fill="url(#mini-grid)"/>
      <rect x="780" y="880" width="86" height="48" fill="none" stroke="#ddd" stroke-width=".6"/>
      <text class="txt micro" x="925" y="877" text-anchor="middle">November 2018</text>
      <rect x="880" y="880" width="90" height="48" fill="url(#mini-grid)"/>
      <rect x="880" y="880" width="90" height="48" fill="none" stroke="#ddd" stroke-width=".6"/>
    </g>
    <line class="purple-rule" x1="767" y1="870" x2="767" y2="1451" stroke-width="1.5"/>
    <line class="purple-rule" x1="541" y1="938" x2="983" y2="938" stroke-width="1"/>
    <text class="txt tiny" x="543" y="952">To Do:</text>
    <rect x="541" y="961" width="214" height="470" fill="url(#rules-17)"/>
    <line class="dotted" x1="557" y1="955" x2="557" y2="1430"/>
    <text class="txt tiny" x="772" y="954">Deadlines</text>
    <rect x="769" y="961" width="214" height="105" fill="url(#rules-18)"/>
    <line class="purple-rule" x1="767" y1="1075" x2="983" y2="1075" stroke-width="1.5"/>
    <text class="txt tiny" x="772" y="1089" style="fill:#666">Financial</text>
    <rect x="769" y="1100" width="214" height="100" fill="url(#rules-18)"/>
    <line class="purple-rule" x1="767" y1="1215" x2="983" y2="1215" stroke-width="1.5"/>
    <text class="txt tiny" x="772" y="1229" style="fill:#666">Project</text>
    <rect x="769" y="1240" width="214" height="100" fill="url(#rules-18)"/>
    <line x1="767" y1="1352" x2="983" y2="1352" stroke="var(--ink)" stroke-width="1"/>
    <text class="txt tiny" x="772" y="1366">Other</text>
    <rect x="769" y="1376" width="214" height="60" fill="url(#rules-18)"/>
  </g>

  <!-- ========== QUOTE PAGE ========== -->
  <g class="quote-page">
    <rect class="page" x="1019" y="841" width="458" height="611"/>
    <g class="quote-box">
      <rect x="1065" y="915" width="365" height="220" rx="18" fill="var(--lime)"/>
      <rect x="1065" y="915" width="14" height="220" fill="var(--purple)"/>
      <rect x="1390" y="895" width="40" height="40" fill="var(--purple)"/>
    </g>
    <text class="txt quote-big" text-anchor="middle">
      <tspan x="1252" y="1000">Treat Employees like</tspan>
      <tspan x="1252" y="1039">they make a difference</tspan>
      <tspan x="1252" y="1078">and they will.</tspan>
    </text>
    <g class="reflection-lines">
      <line class="dotted" x1="1065" y1="1243" x2="1418" y2="1243"/>
      <line class="dotted" x1="1065" y1="1259" x2="1418" y2="1259"/>
      <line class="dotted" x1="1065" y1="1275" x2="1418" y2="1275"/>
      <line class="dotted" x1="1065" y1="1291" x2="1418" y2="1291"/>
      <line class="dotted" x1="1065" y1="1307" x2="1418" y2="1307"/>
      <line class="dotted" x1="1065" y1="1323" x2="1418" y2="1323"/>
    </g>
    <rect x="1027" y="1360" width="441" height="84" fill="var(--olive)" stroke="var(--lime)" stroke-width="1.5"/>
  </g>
</svg>
</body>
</html>
```